Design marketing/advertisement email for consulting business

Hello - My company, Brantor-Quisse, is looking for a marketing professional to compose a "marketing" email to be sent to potential professional referral sources. The email should provide an introduction of our company's capabilities and services. We want this marketing piece to invite the recipient to schedule a call with us to further discuss how we could best work together. The email must included elements of our brand. Our website is www.brantorquisse.example and will provide you with all the details about our business as well as our logo, branding, contact details etc. Thanks so much!
Updates
Industry/Entity Type
Business

```html
<!DOCTYPE html>
<html lang="en">
<head>
<meta charset="utf-8">
<title>Brantor-Quisse – Senior Housing Consulting</title>
<link rel="stylesheet" href="https://fonts.googleapis.com/css2?family=Arimo:wght@400;700&family=Tinos&display=swap">
<style>
  :root {
    --backdrop: #ae9a73;
    --paper: #ffffff;
    --footer: #c8c6c3;
    --pill: #aaa9a7;
    --band: #c9c7c4;
    --ink: #3a3a42;
    --body-ink: #44444a;
    --coral: #de6c51;
    --peach: #f8ad82;
    --peach-edge: #e86f4f;
    --tile-edge: #f2a07a;
    --rule: #9c9a98;
  }
  * { margin: 0; padding: 0; box-sizing: border-box; }
  html, body { width: 1200px; height: 1200px; overflow: hidden; }
  body { background: var(--backdrop); position: relative; font-family: "Arimo", Arial, sans-serif; }

  .email { position: absolute; left: 241px; top: 151px; width: 720px; height: 900px; background: var(--paper); overflow: hidden; }

  .brand { position: absolute; left: 29px; top: 29px; display: flex; align-items: center; gap: 14px; }
  .brand-square { width: 62px; height: 62px; background: var(--coral); }
  .brand-name { font-family: "Arimo", Arial, sans-serif; font-size: 36px; color: var(--ink); letter-spacing: -0.5px; }

  .intro {
    position: absolute; left: 28px; top: 130px; width: 659px;
    font-family: "Tinos", "Times New Roman", serif; font-size: 18.2px; line-height: 22.6px;
    color: var(--body-ink); text-align: justify; text-indent: 77px; hyphens: auto;
  }
  .intro .initial { font-size: 40px; line-height: 18px; }

  .services-heading { position: absolute; left: 46px; top: 362px; font-size: 24px; color: #1e1e22; font-weight: 400; }

  .services-band { position: absolute; left: 17px; top: 438px; width: 685px; height: 60px; background: var(--band); }

  .service {
    position: absolute; top: 403px; width: 215px; height: 215px;
    display: flex; flex-direction: column; align-items: center; justify-content: flex-start;
    text-align: center; color: #fff; border: 2px solid; box-shadow: 3px 4px 5px rgba(0,0,0,0.35);
    padding-top: 70px;
  }
  .service h3 { font-size: 28.5px; font-weight: 400; line-height: 34px; margin-bottom: 6px; }
  .service p { font-size: 17px; line-height: 21.5px; }
  .service--development { left: 25px; background: var(--ink); border-color: var(--tile-edge); }
  .service--operation { left: 251px; background: var(--coral); border-color: var(--ink); }
  .service--disposition { left: 475px; background: var(--peach); border-color: var(--peach-edge); }

  .contact { position: absolute; left: 0; top: 648px; width: 720px; height: 252px; background: var(--footer); }
  .pill {
    position: absolute; height: 36px; background: var(--pill);
    display: flex; align-items: center; gap: 14px; padding-left: 14px;
    font-size: 26px; color: #111; white-space: nowrap;
  }
  .pill svg { flex: none; }
  .pill--phone { left: 109px; top: 24px; width: 243px; }
  .pill--fax { left: 370px; top: 24px; width: 242px; }
  .pill--email { left: 165px; top: 73px; width: 390px; padding-left: 12px; gap: 12px; font-size: 24px; }

  .contact-rule { position: absolute; left: 31px; top: 132px; width: 659px; height: 2px; background: var(--rule); }

  .office { position: absolute; top: 146px; font-size: 16.5px; line-height: 21.6px; color: #111; font-style: normal; white-space: nowrap; }
  .office--austin { left: 40px; }
  .office--palo-alto { left: 382px; }
</style>
</head>
<body>
  <main class="email">
    <header class="brand">
      <span class="brand-square"></span>
      <span class="brand-name">BrantorQuisse</span>
    </header>

    <p class="intro"><span class="initial">B</span>rantor-Quisse was established to provide senior housing expertise to the real estate investment and development communities. Founded in 2011, Brantor-Quisse offers consulting services to investors, developers and asset managers within the senior housing investment space. Drawing upon the extensive experience of the company’s principals, Maren Colby and Rosa Delfino, Brantor-Quisse is able to offer a wide array of services to ensure successful and profitable senior housing development projects and investments. Brantor-Quisse has offices in Austin, Texas and Palo Alto, California.</p>

    <h2 class="services-heading">SERVICES</h2>
    <div class="services-band"></div>

    <section class="service service--development">
      <h3>Development</h3>
      <p>Acquisition, Planning<br>and Design</p>
    </section>
    <section class="service service--operation">
      <h3>Operation</h3>
      <p>Audits and Assessments</p>
    </section>
    <section class="service service--disposition">
      <h3>Disposition</h3>
      <p>Transition and<br>Exit Strategies</p>
    </section>

    <footer class="contact">
      <div class="pill pill--phone">
        <svg width="30" height="26" viewBox="0 0 30 26" fill="none" stroke="#222" stroke-width="1.6" aria-hidden="true">
          <path d="M2 9c0-4 6-6 13-6s13 2 13 6v2h-6V8H8v3H2z"/>
          <path d="M7 12h16l3 11H4z"/>
          <circle cx="15" cy="17.5" r="3"/>
        </svg>
        <span>512.555.0148</span>
      </div>
      <div class="pill pill--fax">
        <svg width="28" height="28" viewBox="0 0 28 28" fill="none" stroke="#222" stroke-width="1.6" aria-hidden="true">
          <rect x="7" y="2" width="14" height="10"/>
          <path d="M10 5h8M10 8h8"/>
          <rect x="2" y="12" width="24" height="13" rx="1"/>
          <path d="M6 17h16M6 21h16"/>
        </svg>
        <span>512.555.0190</span>
      </div>
      <div class="pill pill--email">
        <svg width="32" height="22" viewBox="0 0 32 22" fill="none" stroke="#222" stroke-width="1.6" aria-hidden="true">
          <rect x="1" y="1" width="30" height="20"/>
          <path d="M1 1l15 12L31 1M1 21l11-10M31 21L20 11"/>
        </svg>
        <span>info@brantorquisse.example</span>
      </div>

      <div class="contact-rule"></div>

      <address class="office office--austin">
        Brantor-Quisse Partners, LLC – Austin<br>
        1420 Cedar Ridge Blvd.<br>
        Suite 410-118<br>
        Austin, TX 78701
      </address>
      <address class="office office--palo-alto">
        Brantor-Quisse Partners, LLC – Palo Alto<br>
        780 Linden Court, #40220<br>
        Palo Alto, CA 94301
      </address>
    </footer>
  </main>
</body>
</html>
```